Popup-Fenster Design für Öffnungszeiten
Zielgruppe
Planung und Realisierung von individuellen Kaminen.
Aufgabenstellung
Für unsere Website www.moosgarten-talbach.de benötigen wir ein Popup-Fenster für die Startseite. Da das Geschäft nicht jeden Tag und zu festen Zeit geöffnet hat, soll der Kunde direkt sehen können, wann das Geschäft das nächste Mal geöffnet hat. Das Popup-Fenster soll auffällig, jedoch nicht überladen und aufdringlich sein. Einen eigenen Entwurf (der mir nicht gefällt) habe ich hochgeladen. Vielleicht benötigt dieser nur noch einen Feinschliff!? Es muss nicht reckteckig sein, ich bin auch für runde oder ovale Formen offen. Der dort eingesetzte Text sollte als Platzhalter eingesetzt werden. Bei Fragen können Sie mir gerne eine Nachricht zukommen lassen.

```html
<!DOCTYPE html>
<html lang="de">
<head>
<meta charset="utf-8">
<title>Moosgarten – Öffnungszeiten</title>
<link rel="stylesheet" href="https://fonts.googleapis.com/css2?family=Raleway:wght@200;400&family=Playfair+Display:ital,wght@1,800&family=Lobster&family=Tinos&display=swap">
<style>
  :root {
    --sidebar-bg: #1c1c1c;
    --nav-text: #a39d8c;
    --gold: #b59a52;
    --gold-light: #e3cc86;
    --gold-dark: #a98f47;
    --popup-top: #3a3a3c;
    --popup-bottom: #050505;
    --white: #ffffff;
    --muted: #c4c4c4;
    --rule: #6a6a6a;
  }
  * { margin: 0; padding: 0; box-sizing: border-box; }
  html, body { width: 1200px; height: 577px; overflow: hidden; background: #000; }
  .page { position: relative; width: 1200px; height: 577px; overflow: hidden; font-family: "Raleway", sans-serif; }

  .sidebar { position: absolute; left: 0; top: 0; width: 263px; height: 577px; background: var(--sidebar-bg); }
  .brand { position: absolute; top: 52px; left: 0; width: 263px; text-align: center; }
  .brand-square { display: block; width: 52px; height: 52px; margin: 0 auto 14px; background: var(--gold); }
  .brand-name { font-weight: 400; font-size: 12.5px; letter-spacing: 3.6px; color: var(--gold); }
  .main-nav { position: absolute; left: 44px; top: 224px; list-style: none; }
  .main-nav li { font-size: 16px; font-weight: 400; color: var(--nav-text); height: 45.7px; line-height: 20px; }
  .legal { position: absolute; left: 44px; top: 538px; font-size: 10.5px; color: var(--nav-text); }

  .hero { position: absolute; left: 263px; top: 0; width: 937px; height: 577px;
    background: linear-gradient(180deg, #5f7790 0%, #a9b8c6 22%, #d8dde2 30%, #6d655a 36%, #8a7c68 52%, #b7ab97 68%, #7e776e 84%, #a28c72 100%); }
  .hero-title { position: absolute; left: 263px; top: 224px; width: 937px; text-align: center;
    font-weight: 200; font-size: 50px; letter-spacing: 0.5px; color: var(--white); white-space: nowrap; }
  .hero-subtitle { position: absolute; left: 263px; top: 284px; width: 932px; text-align: center;
    font-family: "Playfair Display", serif; font-style: italic; font-weight: 800; font-size: 34px; color: var(--white); }
  .hero-cta { position: absolute; left: 619px; top: 508px; font-size: 11px; letter-spacing: 2.6px; color: #e6e2dc; white-space: nowrap; }
  .hero-chevron { position: absolute; left: 724px; top: 532px; }

  .hours-popup { position: absolute; left: 752px; top: 337px; width: 424px; height: 223px; border-radius: 8px;
    background: linear-gradient(180deg, var(--popup-top) 0%, #1a1a1b 45%, var(--popup-bottom) 100%); }
  .popup-banner { position: absolute; left: 742px; top: 337px; width: 444px; height: 44px;
    background: linear-gradient(180deg, var(--gold-light) 0%, var(--gold) 60%, var(--gold-dark) 100%); }
  .popup-title { position: absolute; left: 742px; top: 333px; width: 444px; text-align: center;
    font-family: "Lobster", cursive; font-weight: 400; font-size: 38px; line-height: 50px; color: var(--white);
    text-shadow: 2px 2px 0 #000; }
  .popup-close { position: absolute; left: 1159px; top: 309px; width: 30px; height: 30px; border-radius: 50%;
    background: var(--white); color: #0d1a3a; font-weight: 400; font-size: 16px; line-height: 30px; text-align: center; }

  .popup-body { position: absolute; left: 752px; top: 337px; width: 424px; height: 223px; font-family: "Tinos", serif; color: var(--white); }
  .open-label { position: absolute; left: 0; top: 76px; width: 100%; text-align: center; font-size: 19px; line-height: 24px; white-space: nowrap; }
  .open-times { position: absolute; left: 105px; top: 106px; width: 220px; font-size: 15.5px; line-height: 19px; }
  .time-row { display: flex; white-space: nowrap; }
  .time-day { width: 88px; }
  .popup-rule { position: absolute; left: 41px; top: 159px; width: 343px; height: 1px; background: var(--rule); }
  .more-dates { position: absolute; left: 0; top: 166px; width: 100%; text-align: center; font-size: 15px; line-height: 21px; color: var(--muted); }
</style>
</head>
<body>
<div class="page">
  <aside class="sidebar">
    <div class="brand">
      <span class="brand-square"></span>
      <span class="brand-name">MOOSGARTEN</span>
    </div>
    <ul class="main-nav">
      <li>ÜBER UNS</li>
      <li>KAMINÖFEN</li>
      <li>HOLZKAMINE</li>
      <li>GASKAMINE</li>
      <li>AUSSTELLUNG</li>
      <li>KONTAKT</li>
    </ul>
    <div class="legal">Impressum | Datenschutz</div>
  </aside>

  <div class="hero" role="img" aria-label="Foto: hängender schwarzer Kamin vor Panoramafenster mit Berglandschaft"></div>
  <h1 class="hero-title">WILLKOMMEN IM MOOSGARTEN</h1>
  <p class="hero-subtitle">KAMINE FÜRS LEBEN</p>
  <p class="hero-cta">Jetzt Beratungstermin vereinbaren</p>
  <svg class="hero-chevron" width="12" height="8" viewBox="0 0 12 8"><polyline points="1,1 6,6 11,1" fill="none" stroke="#e6e2dc" stroke-width="1.4"/></svg>

  <section class="hours-popup"></section>
  <div class="popup-banner"></div>
  <h2 class="popup-title">Öffnungszeiten</h2>
  <div class="popup-close">X</div>
  <div class="popup-body">
    <p class="open-label">WIR HABEN FÜR SIE GEÖFFNET:</p>
    <div class="open-times">
      <p class="time-row"><span class="time-day">Fr&nbsp; 17.01</span><span>14:00 - 17:00 Uhr</span></p>
      <p class="time-row"><span class="time-day">Sa 18.01</span><span>10:00 - 13:00 Uhr</span></p>
    </div>
    <div class="popup-rule"></div>
    <p class="more-dates">Weitere Termine ansehen Indiviudellen<br>Termin vereinbaren</p>
  </div>
</div>
</body>
</html>
```